Custom Manufacturing Company square space website design

I own a custom manufacturing company that uses precision cutting technology to manufacture project components over a couple industries. We have an industrial CNC router and state of the art edge bander and cut a lot of cabinetry components for cabinet shops, builders, closet companies, ect. We offer design and assembly for any cabinetry or can build cabinets to spec. We also cut components for other industries out of wood, plastics, acryclics, ect. We offer design engineering services, product development protype services. we have a 3D printer farm. We want our communicate trust, dependability, and the value we place on client relationships.

We essentially want a credibility website. Landing page and drops downs for services we offer, capabilites, about us, contact

```html
<!DOCTYPE html>
<html lang="en">
<head>
<meta charset="utf-8">
<title>Northway Millworks</title>
<link rel="stylesheet" href="https://fonts.googleapis.com/css2?family=Lato:wght@400;700;900&family=Oswald:wght@200&display=swap">
<style>
:root{
  --ink:#111111;
  --dark:#1c1c1c;
  --text:#2a2a2a;
  --muted:#8a8a8a;
  --ghost:#e6e6e6;
  --ghost-dark:#3a3a3a;
  --white:#ffffff;
  --shadow:#e9e9e9;
  --green:#4f6b52;
  --wood:#9a7350;
}
*{box-sizing:border-box;margin:0;padding:0}
html,body{width:1200px;height:3887px;overflow:hidden}
body{position:relative;background:var(--white);font-family:'Lato',sans-serif;color:var(--text)}
.abs{position:absolute}
a{color:inherit;text-decoration:none}

/* top bar */
.topbar{left:438px;top:0;width:762px;height:38px;background:var(--ink);clip-path:polygon(12px 0,100% 0,100% 100%,0 100%);color:var(--white);font-size:14px;display:flex;align-items:center;padding-left:32px;gap:26px}
.topbar span{display:flex;align-items:center;gap:10px}
.topbar .social{position:absolute;right:112px;top:10px;width:18px;height:18px;border:2px solid var(--white);border-radius:4px}

/* header */
.brand{left:116px;top:18px;width:170px;display:flex;flex-direction:column;align-items:center;gap:8px}
.brand .mark{width:66px;height:48px;border:3px solid var(--ink)}
.brand .name{font-weight:700;font-size:17px;letter-spacing:2px;color:var(--ink);text-align:center;line-height:1.1}
.nav{left:524px;top:72px;display:flex;align-items:center;font-size:17px;color:var(--text)}
.nav a{margin-right:22px}
.nav a.active{font-weight:700;color:var(--ink)}
.nav i{width:5px;height:5px;border-radius:50%;background:#9b9b9b;margin-right:22px;display:inline-block}

/* hero */
.hero{left:0;top:127px;width:1200px;height:514px;background:linear-gradient(180deg,#eceae4 0%,#d9d6cd 25%,var(--green) 45%,#3f5a43 70%,#7a5a3c 90%,#6a4c32 100%)}
.hero-title{left:0;top:345px;width:1200px;text-align:center;color:var(--white);font-weight:900;font-size:70px;letter-spacing:12px;line-height:1}
.hero-rule{left:300px;top:455px;width:600px;height:4px;background:var(--white)}
.hero-arrow{top:366px;width:36px;height:36px;border:2px solid var(--white);border-radius:50%}
.btn{background:var(--ink);color:var(--white);font-weight:700;font-size:15px;display:flex;align-items:center;justify-content:center;box-shadow:-4px 4px 0 #c9c9c9}

/* shared section heads */
.eyebrow{font-size:24px;color:var(--muted);display:flex;align-items:center;gap:12px}
.eyebrow::after{content:"";width:24px;height:2px;background:var(--muted);margin-top:8px}
.heading{font-size:29px;font-weight:900;color:var(--ink);letter-spacing:-.5px}
.para{font-size:16px;line-height:30px;color:var(--text)}
.ghost-v{font-family:'Oswald',sans-serif;font-weight:200;color:var(--ghost);font-size:96px;letter-spacing:10px;writing-mode:vertical-rl;transform:rotate(180deg);line-height:1}
.ghost-h{font-family:'Oswald',sans-serif;font-weight:200;font-size:110px;letter-spacing:38px;text-align:center;width:1200px;left:0;line-height:1}
.center-eyebrow{left:0;width:1200px;text-align:center;font-size:24px;color:var(--muted)}
.center-eyebrow span::before,.center-eyebrow span::after{content:"";display:inline-block;width:24px;height:2px;background:currentColor;vertical-align:middle;margin:0 12px}
.center-head{left:0;width:1200px;text-align:center;font-size:29px;font-weight:900}

/* framed photos */
.photo-shadow{background:var(--shadow)}
.photo{border:1px solid #cfcfcf}
.corner{width:66px;height:66px;background:var(--white);clip-path:polygon(0 0,100% 0,100% 100%)}

/* services */
.services{left:0;top:1245px;width:1200px;height:773px;background:var(--dark)}
.card{background:var(--white);width:362px;height:394px;box-shadow:6px 6px 0 #2b2b2b;padding:70px 36px 0 36px}
.card .tri{position:absolute;right:0;top:0;width:60px;height:60px;background:var(--ink);clip-path:polygon(0 0,100% 0,100% 100%)}
.card h3{font-size:15.5px;font-weight:700;line-height:30px;color:var(--ink);width:200px;text-transform:uppercase}
.card svg{position:absolute;right:36px;top:52px}
.card p{margin-top:24px;font-size:15.5px;line-height:30px;text-align:justify}

/* portfolio */
.tile{position:absolute}

/* footer */
.footer{left:0;top:3564px;width:1200px;height:323px;background:var(--ink);color:var(--white)}
.footer .fbrand{left:113px;top:48px;width:295px;display:flex;flex-direction:column;align-items:center;gap:14px}
.footer .fbrand .mark{width:122px;height:86px;border:3px solid var(--white)}
.footer .fbrand .name{font-size:28px;font-weight:700;letter-spacing:4px;text-align:center;line-height:1.1}
.flabel{font-size:17px;font-weight:700}
.fline{font-size:16px}
.qlink{display:flex;align-items:center;gap:14px;font-size:16px}
.qlink::before{content:"";border-left:6px solid var(--white);border-top:5px solid transparent;border-bottom:5px solid transparent}
.copy{left:0;top:3856px;width:1200px;text-align:center;font-size:14px;color:var(--white)}
</style>
</head>
<body>

<!-- top contact bar -->
<div class="abs topbar">
  <span><svg width="16" height="16" viewBox="0 0 24 24"><path fill="#fff" d="M6.6 10.8c1.4 2.8 3.8 5.1 6.6 6.6l2.2-2.2c.3-.3.7-.4 1-.2 1.1.4 2.3.6 3.6.6.6 0 1 .4 1 1V20c0 .6-.4 1-1 1C10.6 21 3 13.4 3 4c0-.6.4-1 1-1h3.5c.6 0 1 .4 1 1 0 1.3.2 2.5.6 3.6.1.3 0 .7-.2 1z"/></svg>+1-555-010-2040</span>
  <span><svg width="20" height="15" viewBox="0 0 20 15"><rect width="20" height="15" rx="1" fill="#fff"/><path d="M1 1l9 7 9-7" stroke="#111" stroke-width="1.6" fill="none"/></svg>hello@northwaymillworks.com</span>
  <div class="social" aria-label="Social profile"></div>
</div>

<!-- header -->
<div class="abs brand">
  <div class="mark"></div>
  <div class="name">NORTHWAY<br>MILLWORKS</div>
</div>
<nav class="abs nav">
  <a class="active">Home</a><i></i>
  <a>About Us</a><i></i>
  <a>Services</a><i></i>
  <a>Capabilities</a><i></i>
  <a>Contact Us</a>
</nav>

<!-- hero -->
<div class="abs hero" role="img" aria-label="Photo of a bright kitchen with green cabinets, white tile and wood floor"></div>
<div class="abs hero-title">NORTHWAY<br><span style="font-size:50px;letter-spacing:10px;display:inline-block;margin-top:26px;margin-left:360px">MILLWORKS</span></div>
<div class="abs hero-arrow" style="left:38px"><svg width="32" height="32" viewBox="0 0 32 32"><path d="M18 10l-6 6 6 6" stroke="#fff" stroke-width="2" fill="none"/></svg></div>
<div class="abs hero-arrow" style="left:1120px"><svg width="32" height="32" viewBox="0 0 32 32"><path d="M14 10l6 6-6 6" stroke="#fff" stroke-width="2" fill="none"/></svg></div>
<div class="abs btn" style="left:539px;top:536px;width:130px;height:45px;box-shadow:none">Get Started</div>

<!-- about -->
<div class="abs ghost-v" style="left:22px;top:765px;height:350px">ABOUT</div>
<div class="abs photo-shadow" style="left:128px;top:741px;width:312px;height:434px"></div>
<div class="abs photo" style="left:112px;top:725px;width:312px;height:434px;background:linear-gradient(160deg,#6f8a72 0%,#9a9a92 35%,#5a4c40 70%,#3a3029 100%)" role="img" aria-label="Photo of a kitchen island with bar stools and steel fridge"></div>
<div class="abs corner" style="left:358px;top:725px"></div>
<div class="abs eyebrow" style="left:546px;top:778px">ABOUT</div>
<div class="abs heading" style="left:546px;top:822px">NORTHWAY MILLWORKS</div>
<p class="abs para" style="left:546px;top:876px;width:542px">Lorem ipsum dolor sit amet, consectetur adipiscing elit, sed do eiusmod tempor incididunt ut labore et dolore magna aliqua. Ut enim ad minim veniam, quis nostrud exercitation ullamco laboris nisi ut aliquip ex ea commodo consequat. Duis aute irure dolor in reprehenderit in voluptate velit esse cillum dolore eu fugiat nulla pariatur. Excepteur sint occaecat cupidatat non proident, sunt in culpa qui officia deserunt.</p>
<div class="abs btn" style="left:551px;top:1082px;width:131px;height:44px">Get Started</div>

<!-- services -->
<div class="abs services"></div>
<div class="abs ghost-h" style="top:1300px;color:var(--ghost-dark);font-size:100px">SERVICES</div>
<div class="abs center-eyebrow" style="top:1368px;color:#9a9a9a"><span>OUR SERVICES</span></div>
<div class="abs center-head" style="top:1413px;color:var(--white)">WHAT WE PROVIDE</div>

<div class="abs card" style="left:174px;top:1511px">
  <div class="tri"></div>
  <h3>Design Engineering Services</h3>
  <svg width="62" height="62" viewBox="0 0 62 62" fill="none" stroke="#111" stroke-width="2"><rect x="3" y="10" width="42" height="40"/><path d="M20 40l26-26 6 6-26 26-8 2z"/><path d="M34 58h24V34z"/></svg>
  <p>Lorem ipsum dolor sit amet, consec teturadipiscg elsed do eiusmod tempor incididunt ut labore et dolore magna aliqua. Ut enim ad minim veniam, quis nostrud exercitn ullamco laboris nisi ut aliquip ex ea commo consequat. Duis aute irure dolor in reprehenderit.</p>
</div>
<div class="abs card" style="left:654px;top:1511px">
  <div class="tri"></div>
  <h3>Product Development Prototype Services</h3>
  <svg width="62" height="62" viewBox="0 0 62 62" fill="none" stroke="#111" stroke-width="2"><rect x="2" y="2" width="58" height="54"/><path d="M31 2v54M27 24v8M35 24v8M6 56v4M56 56v4"/></svg>
  <p>Lorem ipsum dolor sit amet, consec teturadipiscg elsed do eiusmod tempor incididunt ut labore et dolore magna aliqua. Ut enim ad minim veniam, quis nostrud exercitn ullamco laboris nisi ut aliquip ex ea commo consequat. Duis aute irure dolor in reprehenderit.</p>
</div>

<!-- special -->
<div class="abs eyebrow" style="left:112px;top:2168px">SPECIAL</div>
<div class="abs heading" style="left:112px;top:2212px">3D PRINTER FARM</div>
<p class="abs para" style="left:112px;top:2266px;width:542px">Lorem ipsum dolor sit amet, consectetur adipiscing elit, sed do eiusmod tempor incididunt ut labore et dolore magna aliqua. Ut enim ad minim veniam, quis nostrud exercitation ullamco laboris nisi ut aliquip ex ea commodo consequat. Duis aute irure dolor in reprehenderit in voluptate velit esse cillum dolore eu fugiat nulla pariatur. Excepteur sint occaecat cupidatat non proident, sunt in culpa qui officia deserunt.</p>
<div class="abs btn" style="left:115px;top:2471px;width:131px;height:45px">Get Started</div>
<div class="abs photo-shadow" style="left:760px;top:2131px;width:312px;height:434px"></div>
<div class="abs photo" style="left:776px;top:2115px;width:312px;height:434px;background:linear-gradient(170deg,#efe7dc 0%,#a07a56 35%,var(--wood) 60%,#5e4330 100%)" role="img" aria-label="Photo of a walk-in closet with wooden shelving and drawers"></div>
<div class="abs corner" style="left:1022px;top:2115px"></div>
<div class="abs ghost-v" style="left:1092px;top:2112px;height:430px">SPECIAL</div>

<!-- portfolio -->
<div class="abs ghost-h" style="top:2668px;color:var(--ghost)">PORTFOLIO</div>
<div class="abs center-eyebrow" style="top:2747px"><span>OUR PORTFOLIO</span></div>
<div class="abs center-head" style="top:2792px;color:var(--ink)">LATEST PROJECTS</div>
<div class="tile" style="left:112px;top:2885px;width:448px;height:297px;background:linear-gradient(160deg,#f2f0ec,#d9d4cb 60%,#8c7158)" role="img" aria-label="Photo of a white kitchen with gold fixtures"></div>
<div class="tile" style="left:568px;top:2885px;width:433px;height:297px;background:linear-gradient(160deg,#e7e9e4,#b9beb6 50%,#4a3a2e)" role="img" aria-label="Photo of a white kitchen with island and dark wood floor"></div>
<div class="tile" style="left:312px;top:3191px;width:432px;height:298px;background:linear-gradient(160deg,#f4f4f2,#d8d8d4 60%,#a8a8a2)" role="img" aria-label="Photo of a white closet system with shelves and drawers"></div>
<div class="tile" style="left:755px;top:3191px;width:332px;height:298px;background:linear-gradient(170deg,#8f8a82,#b3a79a 45%,#9a6b45 80%,#7a5a3e)" role="img" aria-label="Photo of a wooden sideboard against a grey wall"></div>

<!-- footer -->
<footer class="abs footer">
  <div class="abs fbrand">
    <div class="mark"></div>
    <div class="name">NORTHWAY MILLWORKS</div>
  </div>
  <div class="abs fline" style="left:113px;top:238px;display:flex;align-items:center;gap:10px">
    <svg width="16" height="16" viewBox="0 0 24 24"><path fill="#fff" d="M6.6 10.8c1.4 2.8 3.8 5.1 6.6 6.6l2.2-2.2c.3-.3.7-.4 1-.2 1.1.4 2.3.6 3.6.6.6 0 1 .4 1 1V20c0 .6-.4 1-1 1C10.6 21 3 13.4 3 4c0-.6.4-1 1-1h3.5c.6 0 1 .4 1 1 0 1.3.2 2.5.6 3.6.1.3 0 .7-.2 1z"/></svg>
    <b>EMAIL:</b> hello@northwaymillworks.com
  </div>

  <div class="abs flabel" style="left:572px;top:62px;display:flex;align-items:center;gap:12px">
    <svg width="16" height="22" viewBox="0 0 16 22"><path fill="#fff" d="M8 0a8 8 0 0 0-8 8c0 6 8 14 8 14s8-8 8-14a8 8 0 0 0-8-8zm0 11a3 3 0 1 1 0-6 3 3 0 0 1 0 6z"/></svg>CONTACT US:
  </div>
  <div class="abs fline" style="left:572px;top:112px">Northway Millworks</div>
  <div class="abs fline" style="left:572px;top:147px">Address Comes Here</div>
  <div class="abs fline" style="left:572px;top:210px;display:flex;align-items:center;gap:12px">
    <svg width="16" height="16" viewBox="0 0 24 24"><path fill="#fff" d="M6.6 10.8c1.4 2.8 3.8 5.1 6.6 6.6l2.2-2.2c.3-.3.7-.4 1-.2 1.1.4 2.3.6 3.6.6.6 0 1 .4 1 1V20c0 .6-.4 1-1 1C10.6 21 3 13.4 3 4c0-.6.4-1 1-1h3.5c.6 0 1 .4 1 1 0 1.3.2 2.5.6 3.6.1.3 0 .7-.2 1z"/></svg>
    <span><b>PHONE:</b> +1-555-010-2040</span>
  </div>

  <div class="abs flabel" style="left:969px;top:64px">QUICK LINKS:</div>
  <div class="abs qlink" style="left:972px;top:112px">Home</div>
  <div class="abs qlink" style="left:972px;top:147px">About Us</div>
  <div class="abs qlink" style="left:972px;top:182px">Portfolio</div>
  <div class="abs qlink" style="left:972px;top:216px">Contact Us</div>
</footer>
<div class="abs copy">2023 Northway Millworks. All Rights Reserved.</div>

</body>
</html>
```